Agriculture Business Card

I want to use my existing logo and use my tagline of "Don't Guess...Soil Test" on the card. Looking for a double sided card that will really get peoples attention.
Contact Info:
Marlow Field Crop Edge
Calvin Brusk
2917 K Lane
Larkin, NE 68593
402-555-0193
calvin.r.brusk@fieldmailbox.net

```html
<!DOCTYPE html>
<html lang="en">
<head>
<meta charset="utf-8">
<title>Marlow Field Crop Edge – Business Card</title>
<link href="https://fonts.googleapis.com/css2?family=Roboto:wght@400;500;700&family=Orbitron:wght@800&display=swap" rel="stylesheet">
<style>
  :root {
    --backdrop: #2b2b2b;
    --card-white: #ffffff;
    --soil-brown: #a46e4f;
    --logo-brown: #8a5a41;
    --corn-gold: #fbb316;
    --leaf-green: #6cc04a;
    --leaf-deep: #3bb02e;
    --text-white: #ffffff;
  }
  html, body {
    margin: 0;
    width: 1200px;
    height: 1015px;
    overflow: hidden;
    background: var(--backdrop);
    font-family: "Roboto", sans-serif;
  }
  .stage {
    position: relative;
    width: 1200px;
    height: 1015px;
  }
  .card {
    position: absolute;
    left: 240px;
    width: 720px;
    height: 411px;
    box-shadow: 0 12px 30px rgba(0,0,0,.55);
    overflow: hidden;
  }
  .card--front {
    top: 60px;
    background: var(--card-white);
  }
  .card--back {
    top: 540px;
    background: var(--soil-brown);
  }
  .brand {
    position: absolute;
    top: 78px;
    left: 0;
    right: 0;
    display: flex;
    flex-direction: column;
    align-items: center;
    gap: 16px;
  }
  .brand__dot {
    width: 96px;
    height: 96px;
    border-radius: 50%;
    background: var(--corn-gold);
  }
  .brand__name {
    font-weight: 500;
    font-size: 34px;
    color: var(--logo-brown);
    text-align: center;
    line-height: 1.1;
  }
  .tagline {
    position: absolute;
    bottom: 56px;
    left: 0;
    right: 0;
    margin: 0;
    text-align: center;
    font-family: "Orbitron", sans-serif;
    font-weight: 800;
    font-size: 25px;
    color: var(--corn-gold);
    letter-spacing: 2px;
    text-transform: uppercase;
  }
  .artwork {
    position: absolute;
    right: 0;
    top: 0;
    width: 330px;
    height: 300px;
    border-bottom-left-radius: 60px;
    background: linear-gradient(135deg, var(--corn-gold) 0%, var(--corn-gold) 45%, var(--leaf-green) 75%, var(--leaf-deep) 100%);
  }
  .contact {
    position: absolute;
    left: 60px;
    top: 118px;
    color: var(--text-white);
  }
  .contact__name {
    font-weight: 700;
    font-size: 34px;
    color: var(--corn-gold);
    margin: 0 0 18px;
  }
  .contact__line {
    display: flex;
    align-items: center;
    gap: 8px;
    font-size: 19px;
    margin: 2px 0 2px 28px;
  }
  .contact__line svg { flex: none; }
  .contact__company {
    margin: 24px 0 0 56px;
    font-weight: 500;
    font-size: 20px;
    line-height: 1.15;
    color: var(--corn-gold);
  }
  .contact__company span { display: block; padding-left: 20px; }
  .contact__address {
    margin: 0 0 0 86px;
    font-size: 19px;
    line-height: 1.25;
  }
</style>
</head>
<body>
<main class="stage">
  <section class="card card--front" aria-label="Card front">
    <div class="brand">
      <span class="brand__dot" aria-hidden="true"></span>
      <span class="brand__name">Marlow Field Crop<br>Edge</span>
    </div>
    <p class="tagline">Don't Guess...Soil Test</p>
  </section>

  <section class="card card--back" aria-label="Card back">
    <div class="artwork" role="img" aria-label="Large decorative brand artwork in gold and green"></div>
    <div class="contact">
      <h1 class="contact__name">Calvin Brusk</h1>
      <p class="contact__line">
        <svg width="18" height="18" viewBox="0 0 24 24" aria-hidden="true"><path fill="#fbb316" d="M6.6 10.8a15.1 15.1 0 0 0 6.6 6.6l2.2-2.2c.3-.3.7-.4 1-.2 1.1.4 2.3.6 3.6.6.6 0 1 .4 1 1V20c0 .6-.4 1-1 1A17 17 0 0 1 3 4c0-.6.4-1 1-1h3.5c.6 0 1 .4 1 1 0 1.3.2 2.5.6 3.6.1.3 0 .7-.2 1z"/></svg>
        402-555-0193
      </p>
      <p class="contact__line">
        <svg width="18" height="18" viewBox="0 0 24 24" aria-hidden="true"><path fill="#fbb316" d="M2 5h20v14H2z"/><path fill="none" stroke="#a46e4f" stroke-width="2" d="M2 5l10 8 10-8"/></svg>
        calvin.r.brusk@fieldmailbox.net
      </p>
      <p class="contact__company">Marlow Field Crop<span>Edge</span></p>
      <p class="contact__address">2917 K Lane, Larkin<br>NE 68593</p>
    </div>
  </section>
</main>
</body>
</html>
```